Custom Cabinet Shop Needs a website design

Hi,
We need a website for a Custom Cabinet Shop and Cabinet parts manufacturing business.
The business has two sides to it. One side provides custom Kitchens, vanities, entertainment units, offices and what not to homeowners and contractors.
The 2nd side of the business provides built to order cabinet boxes and other parts required to put together a project to other cabinet shops, small contractors looking to install there own cabinets.
Website will need a Gallery to display work.
Color scheme to go well with logo.
current website is www.brambleoakcustomcabinets.com
being changed to www.brambleoak.ca
Logo Included in attached files.
Tagline "Joinery with Spirit"
Mission Statement "Our passion is to deliver inspired cabinetry solutions to suit all your needs, supported by our phenomenal star class customer service"
The website should convey quality and professionalism.
Thank you.
Homeowners/ Contractors
Entertainment

```html
<!DOCTYPE html>
<html lang="en">
<head>
<meta charset="utf-8">
<title>Bramble Oak Custom Cabinets</title>
<link rel="stylesheet" href="https://fonts.googleapis.com/css2?family=Open+Sans:wght@400;600;700&family=Titillium+Web:wght@700&display=swap">
<style>
  :root {
    --accent: #e0461c;
    --ink: #333333;
    --muted: #7a7a7a;
    --nav: #8a8a8a;
    --rule: #dcdcdc;
    --footer-bg: #212121;
    --footer-text: #a8a8a8;
    --footer-sep: #555555;
    --arrow-bg: rgba(90, 90, 90, 0.75);
    --white: #ffffff;
  }
  * { margin: 0; padding: 0; box-sizing: border-box; }
  html, body { width: 1167px; height: 1200px; overflow: hidden; background: var(--white); }
  body { position: relative; font-family: "Open Sans", Arial, sans-serif; color: var(--ink); }

  .site-header { position: absolute; left: 0; top: 0; width: 1167px; height: 130px; }
  .brand { position: absolute; left: 97px; top: 45px; display: flex; align-items: center; gap: 10px; }
  .brand-mark { width: 22px; height: 22px; background: var(--accent); }
  .brand-name { font-size: 26px; font-weight: 700; color: #111111; letter-spacing: 0.5px; }

  .contact-phones { position: absolute; right: 98px; top: 25px; display: flex; align-items: center; gap: 6px; font-size: 16px; }
  .contact-phones .phone { color: var(--accent); }
  .contact-phones .or { color: var(--nav); margin: 0 6px; }
  .contact-phones svg { margin-right: 2px; }

  .main-nav { position: absolute; right: 98px; top: 80px; display: flex; gap: 33px; }
  .main-nav a { font-size: 11px; text-decoration: none; color: var(--nav); text-transform: uppercase; }
  .main-nav a.is-active { color: var(--accent); }

  .hero { position: absolute; left: 0; top: 130px; width: 1167px; height: 509px;
    background: linear-gradient(100deg, #7c8a86 0%, #2e2224 30%, #2a1f22 60%, #8a6a60 85%, #b08a7a 100%); }
  .hero-photo { position: absolute; inset: 0; }
  .hero-counter { position: absolute; left: 0; top: 180px; width: 660px; height: 130px;
    background: linear-gradient(180deg, #d9dedc 0%, #c9cdcb 100%); opacity: 0.85; }
  .slider-arrow { position: absolute; top: 233px; width: 32px; height: 42px; background: var(--arrow-bg);
    display: flex; align-items: center; justify-content: center; }
  .slider-arrow.prev { left: 0; }
  .slider-arrow.next { right: 0; }
  .hero-tagline { position: absolute; left: 404px; top: 428px; width: 355px; height: 42px;
    background: rgba(30, 28, 30, 0.9); color: var(--white); display: flex; align-items: center; justify-content: center;
    font-family: "Titillium Web", "Open Sans", sans-serif; font-weight: 700; font-size: 31px; text-transform: uppercase; letter-spacing: 0.5px; }

  .welcome { position: absolute; left: 0; top: 690px; width: 1167px; text-align: center; }
  .welcome h1 { font-size: 25px; font-weight: 400; color: var(--accent); text-transform: uppercase; letter-spacing: 0.3px; }
  .welcome p { margin: 6px auto 0; width: 620px; font-size: 14px; line-height: 20px; color: var(--muted); }

  .section-rule { position: absolute; left: 95px; top: 812px; width: 975px; height: 2px; background: var(--rule); }

  .gallery-title { position: absolute; left: 97px; top: 856px; font-size: 26px; font-weight: 400; color: var(--ink); }
  .gallery-controls { position: absolute; left: 1038px; top: 863px; display: flex; gap: 2px; }
  .gallery-controls span { width: 14px; height: 18px; background: #8d8d8d; border-radius: 9px; display: flex; align-items: center; justify-content: center; }
  .gallery-grid { position: absolute; left: 97px; top: 909px; display: flex; gap: 13px; }
  .gallery-item { width: 233px; height: 141px; }
  .gallery-item.kitchen-dark { background: linear-gradient(135deg, #7b6a5a, #3a2a24 55%, #a78a6a); }
  .gallery-item.media-wall { background: linear-gradient(135deg, #b9a898, #4a2620 60%, #8a6a5a); }
  .gallery-item.built-in { background: linear-gradient(135deg, #d8cfb8, #2a201e 50%, #e0d8c0); }
  .gallery-item.kitchen-white { background: linear-gradient(135deg, #d6c8b6, #5a3a30 55%, #222222); }

  .site-footer { position: absolute; left: 0; top: 1100px; width: 1167px; height: 100px; background: var(--footer-bg); }
  .footer-nav { position: absolute; left: 97px; top: 29px; display: flex; font-size: 11px; }
  .footer-nav a { color: var(--footer-text); text-decoration: none; }
  .footer-nav .sep { color: var(--footer-sep); margin: 0 10px; }
  .copyright { position: absolute; left: 97px; top: 57px; font-size: 11px; color: var(--footer-text); word-spacing: 2px; }
  .social { position: absolute; left: 1009px; top: 1138px; display: flex; gap: 12px; }
  .social span { width: 24px; height: 24px; border-radius: 50%; }
  .social .first { background: #2f4f9a; }
  .social .second { background: #2fa6e0; }
</style>
</head>
<body>
  <header class="site-header">
    <div class="brand">
      <span class="brand-mark"></span>
      <span class="brand-name">BRAMBLE OAK</span>
    </div>
    <div class="contact-phones">
      <svg width="13" height="13" viewBox="0 0 24 24" aria-hidden="true"><path fill="#111" d="M6.6 10.8a15.1 15.1 0 0 0 6.6 6.6l2.2-2.2c.3-.3.7-.4 1-.2 1.1.4 2.3.6 3.6.6.6 0 1 .4 1 1V20c0 .6-.4 1-1 1A17 17 0 0 1 3 4c0-.6.4-1 1-1h3.5c.6 0 1 .4 1 1 0 1.3.2 2.5.6 3.6.1.3 0 .7-.2 1z"/></svg>
      <span class="phone">555-210-4837</span>
      <span class="or">Or</span>
      <span class="phone">555-396-7021</span>
    </div>
    <nav class="main-nav">
      <a href="#" class="is-active">Home</a>
      <a href="#">Gallery</a>
      <a href="#">Services</a>
      <a href="#">Warranty</a>
      <a href="#">Contact</a>
    </nav>
  </header>

  <section class="hero">
    <div class="hero-photo" role="img" aria-label="Dark wood-grain kitchen cabinets with long steel handles along a pale wall">
      <div class="hero-counter"></div>
    </div>
    <span class="slider-arrow prev"><svg width="12" height="24" viewBox="0 0 12 24"><path d="M11 1 1 12l10 11" fill="none" stroke="#fff" stroke-width="1.5"/></svg></span>
    <span class="slider-arrow next"><svg width="12" height="24" viewBox="0 0 12 24"><path d="m1 1 10 11L1 23" fill="none" stroke="#fff" stroke-width="1.5"/></svg></span>
    <div class="hero-tagline">Joinery with Spirit</div>
  </section>

  <section class="welcome">
    <h1>Welcome to Bramble Oak Custom Cabinets</h1>
    <p>Our passion is to deliver inspired cabinetry solutions to suit all your needs, supported by our phenomenal star class customer service.</p>
  </section>

  <div class="section-rule"></div>

  <h2 class="gallery-title">Our Gallery</h2>
  <div class="gallery-controls">
    <span><svg width="6" height="8" viewBox="0 0 6 8"><path d="M5 0 0 4l5 4z" fill="#fff"/></svg></span>
    <span><svg width="6" height="8" viewBox="0 0 6 8"><path d="m1 0 5 4-5 4z" fill="#fff"/></svg></span>
  </div>
  <div class="gallery-grid">
    <div class="gallery-item kitchen-dark" role="img" aria-label="Dark kitchen with island, pendant lights and steel fridge"></div>
    <div class="gallery-item media-wall" role="img" aria-label="Cherry media console below a wall-mounted television"></div>
    <div class="gallery-item built-in" role="img" aria-label="Dark built-in entertainment wall unit with shelving"></div>
    <div class="gallery-item kitchen-white" role="img" aria-label="White kitchen with large island and bar stools"></div>
  </div>

  <footer class="site-footer">
    <nav class="footer-nav">
      <a href="#">Home</a><span class="sep">|</span>
      <a href="#">Gallery</a><span class="sep">|</span>
      <a href="#">Services</a><span class="sep">|</span>
      <a href="#">Warranty</a><span class="sep">|</span>
      <a href="#">Contact</a>
    </nav>
    <p class="copyright">Copyright © 2015 Bramble Oak Custom Cabinets. All rights reserved.</p>
  </footer>
  <div class="social">
    <span class="first" role="img" aria-label="Social profile link"></span>
    <span class="second" role="img" aria-label="Social profile link"></span>
  </div>
</body>
</html>
```